Stylish new business card needed!

Hello everyone! I am in need of a new business card design for an alarm company here in Hurricane WV. I have all fonts, color codes and logos provided for you use! We are a young company and like the style of a clean sleek looking business card. Would like it double sided, one side holding the logo and the other with your design!
Target Market(s)
The people that are looking for the newest tech for home automation and security
Industry/Entity Type
Alarm services; Home automation
Contact Information for Business Card
Name of person; position (Sales; Installer); Phone Number (555.418.7260); Employee cell Number; Website (www.GuardedByVelk.example); Employee Email; Double sided
Look and feel
Each slider illustrates characteristics of the customer's brand and the style your logo design should communicate.

```html
<!DOCTYPE html>
<html lang="en">
<head>
<meta charset="utf-8">
<title>Velk Business Card</title>
<link href="https://fonts.googleapis.com/css2?family=Montserrat:wght@400;700&display=swap" rel="stylesheet">
<style>
  :root {
    --orange: #f59254;
    --orange-deep: #b5652f;
    --grey: #9b9b9b;
    --white: #ffffff;
    --backdrop: #e9e9e9;
  }
  * { margin: 0; padding: 0; box-sizing: border-box; }
  html, body { width: 1200px; height: 912px; overflow: hidden; }
  body {
    background: var(--backdrop);
    font-family: "Montserrat", sans-serif;
    display: flex;
    flex-direction: column;
    align-items: center;
    justify-content: center;
    gap: 56px;
  }
  .card {
    position: relative;
    width: 640px;
    height: 366px;
    border-radius: 16px;
    overflow: hidden;
  }
  .card-front {
    background: var(--orange);
    display: flex;
    align-items: center;
    justify-content: center;
  }
  .front-wordmark {
    font-size: 112px;
    font-weight: 400;
    letter-spacing: 6px;
    color: var(--orange-deep);
  }
  .card-back { background: var(--white); }
  .back-shapes { position: absolute; inset: 0; }
  .back-logo {
    position: absolute;
    left: 48px;
    top: 52px;
    display: flex;
    align-items: center;
    gap: 14px;
  }
  .back-logo-dot {
    width: 26px;
    height: 26px;
    border-radius: 50%;
    background: var(--orange);
  }
  .back-wordmark {
    font-size: 72px;
    font-weight: 400;
    letter-spacing: 4px;
    color: var(--grey);
  }
  .contact {
    position: absolute;
    right: 30px;
    top: 130px;
    text-align: right;
    color: var(--white);
  }
  .contact-name { font-size: 22px; font-weight: 700; line-height: 1.1; }
  .contact-role { font-size: 12px; margin-bottom: 10px; }
  .contact-address { font-size: 12px; line-height: 1.45; margin-bottom: 8px; }
  .contact-line {
    font-size: 12px;
    line-height: 1.6;
    display: flex;
    justify-content: flex-end;
    align-items: center;
    gap: 7px;
  }
  .contact-icon { width: 12px; height: 12px; flex: none; }
</style>
</head>
<body>
  <section class="card card-front">
    <span class="front-wordmark">VELK</span>
  </section>

  <section class="card card-back">
    <svg class="back-shapes" viewBox="0 0 640 366" width="640" height="366" aria-hidden="true">
      <path d="M640,50 C480,62 390,100 366,190 C344,280 280,304 0,304 L0,366 L640,366 Z" fill="var(--orange)"/>
      <path d="M640,34 C478,46 378,88 354,172" fill="none" stroke="var(--grey)" stroke-width="6"/>
      <path d="M354,236 C330,312 290,334 240,342" fill="none" stroke="var(--white)" stroke-width="2.5"/>
    </svg>

    <div class="back-logo">
      <span class="back-logo-dot"></span>
      <span class="back-wordmark">VELK</span>
    </div>

    <div class="contact">
      <p class="contact-name">Dana Corwell</p>
      <p class="contact-role">Sales/Installer</p>
      <p class="contact-address">418 Ridgeview Lane<br>Marlow County Name 7704</p>
      <p class="contact-line">555.418.7260
        <svg class="contact-icon" viewBox="0 0 16 16" aria-hidden="true"><path d="M3 1h3l1.5 4-2 1.2a9 9 0 0 0 4.3 4.3L11 8.5l4 1.5v3a2 2 0 0 1-2 2A12 12 0 0 1 1 3a2 2 0 0 1 2-2z" fill="var(--white)"/></svg>
      </p>
      <p class="contact-line">info@GuardedByVelk.example
        <svg class="contact-icon" viewBox="0 0 16 16" aria-hidden="true"><rect x="1" y="3" width="14" height="10" fill="var(--white)"/><path d="M1 3l7 6 7-6" fill="none" stroke="var(--orange)" stroke-width="1.4"/></svg>
      </p>
      <p class="contact-line">www.GuardedByVelk.example
        <svg class="contact-icon" viewBox="0 0 16 16" aria-hidden="true"><circle cx="8" cy="8" r="6.5" fill="none" stroke="var(--white)" stroke-width="1.5"/><path d="M1.5 8h13M8 1.5c-3 3.5-3 9.5 0 13M8 1.5c3 3.5 3 9.5 0 13" fill="none" stroke="var(--white)" stroke-width="1.2"/></svg>
      </p>
    </div>
  </section>
</body>
</html>
```